RWT Fittings Ltd Business Cards

We need a business card with our business logo. We provide window and door installations on high-rises in west coast British Colombia, Canada.

I would like my business information and details on one side of the card, and the other side the company name with logo

Target Market(s)

General Contractors

Industry/Entity Type

Construction

Contact Information for Business Card

one side i want my company name and logo in the dark theme logo that i provided

Requirements
Must have
• Marco Peltieri, 16045518293, RWTFittings@mailbox-demo.com, 1407-5194 Linden Row Burnaby BC, V5H 2K9, Owner & Manager

```html
<!DOCTYPE html>
<html lang="en">
<head>
<meta charset="utf-8">
<title>RWT Fittings Ltd – Business Cards</title>
<link rel="stylesheet" href="https://fonts.googleapis.com/css2?family=Roboto:wght@400;500;700;900&display=swap">
<style>
  :root {
    --stage: #232325;
    --card: #1f1f22;
    --blue: #27a9e1;
    --grey: #9a9a9a;
    --white: #ffffff;
    --pattern-dark: #18181a;
    --pattern-light: #3a3a3e;
  }
  * { margin: 0; padding: 0; box-sizing: border-box; }
  html, body {
    width: 1200px; height: 780px; overflow: hidden;
    background: var(--stage);
    font-family: "Roboto", Arial, sans-serif;
  }
  .sheet {
    position: relative; width: 1200px; height: 780px;
    display: flex; align-items: center; justify-content: center; gap: 40px;
  }
  .card {
    position: relative; width: 540px; height: 310px;
    background: var(--card);
    border-radius: 16px;
    border: 3px solid var(--blue);
    overflow: hidden;
    box-shadow: 0 18px 40px rgba(0,0,0,.55);
  }

  /* Back side */
  .card-back__pattern {
    position: absolute; inset: 0;
    background: linear-gradient(160deg, var(--pattern-light) 0%, var(--pattern-dark) 55%, var(--card) 100%);
  }
  .card-back__name {
    position: absolute; right: 34px; bottom: 56px;
    color: var(--blue); font-weight: 700; font-size: 15px; letter-spacing: .5px;
  }

  /* Front side */
  .brand {
    position: absolute; left: 34px; top: 128px;
    color: var(--blue); font-weight: 700; font-size: 27px; letter-spacing: .3px;
  }
  .divider {
    position: absolute; left: 262px; top: 58px;
    width: 2px; height: 170px; background: var(--white);
  }
  .contact {
    position: absolute; left: 290px; top: 44px; color: var(--white);
  }
  .contact__name { font-weight: 900; font-size: 25px; line-height: 1; }
  .contact__first { color: var(--blue); }
  .contact__last { color: var(--grey); }
  .contact__title { font-weight: 700; font-size: 13px; margin-top: 4px; }
  .contact__address { font-size: 12.5px; line-height: 1.35; margin-top: 16px; }
  .contact__line {
    display: flex; align-items: center; gap: 8px;
    font-size: 12.5px; margin-top: 4px;
  }
  .contact__lines { margin-top: 14px; }
  .contact__line svg { width: 14px; height: 14px; flex: none; }

  .band-blue {
    position: absolute; left: 0; bottom: 22px;
    width: 340px; height: 16px; background: var(--blue);
  }
  .band-mark {
    position: absolute; left: 346px; bottom: 22px;
    width: 26px; height: 26px; background: var(--blue);
  }
  .band-grey {
    position: absolute; left: 378px; right: 0; bottom: 50px;
    height: 14px; background: var(--grey);
  }
</style>
</head>
<body>
<main class="sheet">

  <section class="card card-back" aria-label="Card back">
    <div class="card-back__pattern" role="img" aria-label="Repeating pattern of the company building mark"></div>
    <span class="card-back__name">RWT Fittings Ltd</span>
  </section>

  <section class="card card-front" aria-label="Card front">
    <span class="brand">RWT Fittings Ltd</span>
    <span class="divider"></span>

    <div class="contact">
      <p class="contact__name"><span class="contact__first">Marco</span> <span class="contact__last">Peltieri</span></p>
      <p class="contact__title">Owner &amp; Manager</p>
      <p class="contact__address">1407-5194 Linden Row<br>Burnaby BC, V5H 2K9</p>
      <div class="contact__lines">
        <p class="contact__line">
          <svg viewBox="0 0 24 24" aria-hidden="true"><path fill="#27a9e1" d="M6.6 10.8a15 15 0 0 0 6.6 6.6l2.2-2.2a1 1 0 0 1 1-.25 11.4 11.4 0 0 0 3.6.57 1 1 0 0 1 1 1V20a1 1 0 0 1-1 1A17 17 0 0 1 3 4a1 1 0 0 1 1-1h3.5a1 1 0 0 1 1 1c0 1.25.2 2.45.57 3.57a1 1 0 0 1-.25 1z"/></svg>
          1 604 551 8293
        </p>
        <p class="contact__line">
          <svg viewBox="0 0 24 24" aria-hidden="true"><path fill="#27a9e1" d="M3 5h18a1 1 0 0 1 1 1v12a1 1 0 0 1-1 1H3a1 1 0 0 1-1-1V6a1 1 0 0 1 1-1zm9 7.5L4 7.2V8l8 5.3L20 8v-.8z"/></svg>
          RWTFittings@mailbox-demo.com
        </p>
      </div>
    </div>

    <span class="band-blue"></span>
    <span class="band-mark"></span>
    <span class="band-grey"></span>
  </section>

</main>
</body>
</html>
```